Create American style design suitable for consumers in Europe and America

We need a professional universal neutral design, which can be applied to all personal care tools, regardless of male and female, and the color matching needs to be matched by designers themselves.
Updates

设计质量低

Target Market(s)

Europe and America

Industry/Entity Type

personal care tools

Font styles to use
Serif
Sans Serif
Script

Requirements
Must have
• personal beauty care tool,like nail clipper,tweezer,scissors
Nice to have
• The copywriter plans on the packaging design can be applied to all personal care tools
Should not have
• Not designed for a single product, but for a whole personal care tool

```html
<!DOCTYPE html>
<html lang="en">
<head>
<meta charset="utf-8">
<title>Lumen Care – Nail Clipper Packaging</title>
<link rel="stylesheet" href="https://fonts.googleapis.com/css2?family=Montserrat:wght@400;500;800&family=Oswald:wght@500;600;700&display=swap">
<style>
  :root {
    --stage: #e3e3e3;
    --paper: #fbfbf9;
    --teal: #3e9a8c;
    --teal-soft: #a9d8d0;
    --peach: #f3c9b8;
    --sand: #f2d3a3;
    --gold: #d6963c;
    --ink: #2a2a2a;
  }
  * { margin: 0; padding: 0; box-sizing: border-box; }
  html, body { width: 1200px; height: 1056px; overflow: hidden; }
  body {
    background: var(--stage);
    font-family: "Montserrat", sans-serif;
    color: var(--ink);
    position: relative;
  }
  .dieline {
    position: absolute;
    top: 78px; left: 120px;
    display: flex; gap: 20px;
  }
  .panel {
    position: relative;
    height: 900px;
    background: var(--paper);
    overflow: hidden;
    box-shadow: 0 2px 10px rgba(0,0,0,.08);
  }
  .panel-side { width: 380px; }
  .panel-front { width: 560px; }
  .pattern {
    position: absolute; inset: 0;
    background:
      radial-gradient(circle at 20% 18%, rgba(242,211,163,.55), transparent 30%),
      radial-gradient(circle at 78% 22%, rgba(169,216,208,.55), transparent 32%),
      radial-gradient(circle at 30% 55%, rgba(243,201,184,.45), transparent 30%),
      radial-gradient(circle at 80% 62%, rgba(169,216,208,.45), transparent 30%),
      radial-gradient(circle at 25% 86%, rgba(242,211,163,.45), transparent 28%),
      var(--paper);
  }
  .base-band {
    position: absolute; left: 0; right: 0; bottom: 0;
    height: 16px; background: var(--gold);
  }
  .brand {
    position: absolute; left: 0; right: 0; text-align: center;
    font-weight: 400; color: var(--ink); letter-spacing: .02em;
  }
  .panel-front .brand { top: 360px; font-size: 60px; }
  .panel-side .brand { top: 70px; font-size: 34px; }
  .product-name {
    position: absolute; left: 0; right: 0; text-align: center;
    color: var(--teal);
  }
  .panel-front .product-name {
    top: 730px; font-weight: 800; font-size: 64px; letter-spacing: .01em;
  }
  .panel-side .product-name {
    top: 130px; font-family: "Oswald", sans-serif; font-weight: 600; font-size: 60px;
  }
  .tagline {
    position: absolute; left: 0; right: 0; text-align: center; font-weight: 500;
  }
  .panel-front .tagline { top: 812px; font-size: 26px; }
  .panel-side .tagline { top: 218px; font-size: 20px; }
  .copy-box {
    position: absolute; top: 262px; left: 26px; right: 26px;
    border: 1.5px solid var(--gold); border-radius: 18px;
    background: rgba(255,255,255,.85);
    padding: 20px 18px 64px;
    font-family: "Oswald", sans-serif; font-weight: 500;
    font-size: 13.5px; line-height: 1.45; text-align: justify;
  }
  .badges {
    position: absolute; top: 560px; left: 0; right: 0;
    display: flex; justify-content: center; gap: 30px;
  }
  .badge {
    width: 92px; height: 92px; border-radius: 50%;
    border: 1.5px solid var(--gold); background: var(--paper);
    display: flex; align-items: center; justify-content: center; text-align: center;
    font-family: "Oswald", sans-serif; font-weight: 700; font-size: 12px; line-height: 1.15;
  }
  .contact {
    position: absolute; top: 720px; left: 0; right: 0; text-align: center;
    font-family: "Oswald", sans-serif; font-weight: 600; font-size: 15px; line-height: 1.5;
  }
  .contact-title { color: var(--gold); font-size: 17px; margin-bottom: 4px; }
</style>
</head>
<body>
  <main class="dieline">
    <section class="panel panel-side">
      <div class="pattern" role="img" aria-label="Soft pastel pattern of cross-hatched teal, peach and sand dots"></div>
      <div class="brand">Lumen Care</div>
      <h2 class="product-name">NAIL CLIPPER</h2>
      <p class="tagline">Personal beauty care tool</p>
      <p class="copy-box">Lorem Ipsum is simply dummy text of the printing and typesetting industry. Lorem Ipsum has been the industry's standard dummy text ever since the 1500s, when an unknown printer took a galley of type and scrambled it to make a type specimen book. It has survived not only five centuries, but also the leap into electronic typesetting, remaining essentially unchanged. It was popularised in the 1960s with the release of Vellora sheets containing Lorem Ipsum passages, and more recently with desktop publishing software like Quillset Page</p>
      <div class="badges">
        <div class="badge">High<br>Quality<br>Stainless<br>Steel</div>
        <div class="badge">100%<br>Satisfaction<br>Guaranteed</div>
      </div>
      <div class="contact">
        <div class="contact-title">ANY QUESTIONS? CONTACT US</div>
        <div>PH: (555) 014-2290</div>
        <div>E: hello@lumencare.example</div>
        <div>W: www.lumencare.example</div>
      </div>
      <div class="base-band"></div>
    </section>
    <section class="panel panel-front">
      <div class="pattern" role="img" aria-label="Soft pastel pattern of cross-hatched teal, peach and sand dots"></div>
      <div class="brand">Lumen Care</div>
      <h1 class="product-name">NAIL CLIPPER</h1>
      <p class="tagline">Personal beauty care tool</p>
      <div class="base-band"></div>
    </section>
  </main>
</body>
</html>
```